Marlow Estate Fixers (Handyman / Home Improvement Company)

Looking for a double sided professional looking business card with Logo attached to be highlighted on one side and throwing in an image of a handyman as an option would be nice to see as well. We are a company focused on providing quality Handyman and Home improvement services in a timely manner that is done right the first time with integrity

Industry/Entity Type

Handyman / Home Improvement

Contact Information for Business Card

(LOGO, Name, Mobile and office phone numbers, email) on front side of card, (the words "The SOLUTION to all of your Handyman and Home Improvement needs" followed by "Family Owned and Operated" at the very bottom) on the back.

Colors
EB3D1F
EC4F4E
F09395
F8D3D4
FCEDEE

Requirements
Must have
• Red, Gray, Black Color scheme
Should not have
• No Yellow or Blue colors

```html
<!DOCTYPE html>
<html lang="en">
<head>
<meta charset="utf-8">
<title>Marlow Estate Fixers – Business Card</title>
<link rel="stylesheet" href="https://fonts.googleapis.com/css2?family=Montserrat:wght@400;600;700&family=Anton&display=swap">
<style>
  :root {
    --stage: #1c1c1c;
    --card-black: #000000;
    --brand-red: #e8292e;
    --white: #ffffff;
    --shadow: rgba(0,0,0,0.55);
    --figure-light: #c9c9c9;
    --figure-dark: #8a8a8a;
  }
  * { margin: 0; padding: 0; box-sizing: border-box; }
  html, body { width: 1200px; height: 1059px; overflow: hidden; }
  body { background: var(--stage); position: relative; font-family: "Montserrat", sans-serif; color: var(--white); }

  .card { position: absolute; border-radius: 24px; box-shadow: -6px 6px 14px var(--shadow); overflow: hidden; }

  /* Front */
  .card-front { left: 262px; top: 94px; width: 714px; height: 409px; background: var(--card-black); }
  .brand-lockup { position: absolute; right: 28px; top: 104px; display: flex; align-items: center; gap: 10px; }
  .brand-mark { width: 22px; height: 22px; border-radius: 50%; background: var(--brand-red); }
  .brand-name { font-weight: 700; font-size: 27px; color: var(--brand-red); white-space: nowrap; }
  .person-name { position: absolute; left: 35px; top: 253px; font-weight: 600; font-size: 27px; color: var(--brand-red); letter-spacing: 0.3px; }
  .person-role { position: absolute; left: 35px; top: 297px; font-weight: 400; font-size: 19px; }
  .divider { position: absolute; left: 35px; top: 336px; width: 648px; height: 2px; background: var(--white); }
  .contact-item { position: absolute; top: 352px; height: 24px; display: flex; align-items: center; gap: 12px; font-size: 19px; white-space: nowrap; }
  .contact-item svg { fill: var(--brand-red); flex: none; }
  .contact-mobile { left: 38px; }
  .contact-office { left: 245px; }
  .contact-email { left: 442px; }

  /* Back */
  .card-back { left: 262px; top: 529px; width: 717px; height: 410px; background: var(--brand-red); }
  .tagline { position: absolute; left: 20px; top: 92px; width: 400px; text-align: center; line-height: 1; }
  .tagline-lead { display: block; font-weight: 700; font-size: 29px; letter-spacing: 0.2px; }
  .tagline-big { display: block; font-family: "Anton", sans-serif; font-size: 49px; line-height: 56px; margin-top: 4px; }
  .tagline-big + .tagline-big { margin-top: 0; }
  .tagline-soft { font-size: 42px; }
  .footer-line { position: absolute; left: 20px; top: 360px; width: 400px; text-align: center; font-weight: 700; font-size: 23px; }
  .handyman-figure { position: absolute; left: 438px; top: 18px; width: 274px; height: 382px; border-radius: 40px 40px 16px 16px; background: linear-gradient(180deg, var(--figure-light), var(--figure-dark)); }
</style>
</head>
<body>
  <section class="card card-front">
    <div class="brand-lockup">
      <span class="brand-mark"></span>
      <span class="brand-name">Marlow Estate Fixers</span>
    </div>
    <h1 class="person-name">Daniel Hartley</h1>
    <p class="person-role">Owner</p>
    <div class="divider"></div>
    <span class="contact-item contact-mobile">
      <svg width="13" height="22" viewBox="0 0 13 22"><path d="M2 0h9a2 2 0 0 1 2 2v18a2 2 0 0 1-2 2H2a2 2 0 0 1-2-2V2a2 2 0 0 1 2-2zm0 3v14h9V3zm4.5 15.5a1.2 1.2 0 1 0 0 2.4 1.2 1.2 0 0 0 0-2.4z"/></svg>
      044-555 010 234
    </span>
    <span class="contact-item contact-office">
      <svg width="20" height="17" viewBox="0 0 20 17"><path d="M1 5c0-3 4-4 9-4s9 1 9 4v2h-4V5H5v2H1zm3 3h12l3 8H1zm4 2v4h4v-4z"/></svg>
      044-555 010 234
    </span>
    <span class="contact-item contact-email">
      <svg width="20" height="15" viewBox="0 0 20 15"><path d="M0 0h20v2l-10 6L0 2zm0 4l10 6 10-6v11H0z"/></svg>
      info@mefix.com
    </span>
  </section>

  <section class="card card-back">
    <p class="tagline">
      <span class="tagline-lead">The SOLUTION to all of</span>
      <span class="tagline-big"><span class="tagline-soft">your</span> Handyman <span class="tagline-soft">and</span></span>
      <span class="tagline-big">Home Improvement</span>
      <span class="tagline-big">Needs</span>
    </p>
    <p class="footer-line">Family Owned and Operated</p>
    <div class="handyman-figure" role="img" aria-label="Cartoon handyman in work overalls holding a pipe wrench and spanner"></div>
  </section>
</body>
</html>
```